Chartered Professional Accounting Firm Needs a Business Card Design

We need a card design for an accounting firm based in Toronto, Ontario. The firm name is Pavel Ostrom Professional Corporation. The owner of the firm is a chartered professional accountant and a certified general accountant. Services of the firm include 60% tax preparation and consulting and 40% financial statements for corporation year-end. We would like a modern design. The color could be black, white, gray, blue or other color to bring more confidence to clients. The logo of the firm should be included in the design. Thanks

Name: Pavel Ostrom, CPA, CGA Address: 47 Maple Crest Rd. Richmond Hill, ON L7K 3B5 Telephone: (416) 562-3907 Fax:(416) 734-2165 Email: pavel@pavelostrom-example.ca

Accounting

```html
<!DOCTYPE html>
<html lang="en">
<head>
<meta charset="UTF-8">
<title>Pavel Ostrom Professional Corporation – Business Card</title>
<link rel="stylesheet" href="https://fonts.googleapis.com/css2?family=Cinzel:wght@600;700&family=Exo+2:wght@400&display=swap">
<style>
  :root {
    --card-dark: #231f20;
    --card-light: #ffffff;
    --brand-blue: #2b3a9a;
    --band-gray: #8b8b8d;
    --rule-gray: #6e6c6d;
    --muted-gray: #9a9899;
    --text-light: #f2f2f2;
    --page-bg: #e7e4df;
  }
  * { box-sizing: border-box; margin: 0; padding: 0; }
  html, body {
    width: 1200px; height: 870px; overflow: hidden;
    background: var(--page-bg);
  }
  .sheet {
    position: relative; width: 1200px; height: 870px;
    display: flex; justify-content: center; align-items: center; gap: 72px;
  }
  .card {
    position: relative; width: 434px; height: 760px;
    border-radius: 6px; overflow: hidden;
    box-shadow: 0 6px 22px rgba(0,0,0,.18);
  }
  .card--front { background: var(--card-dark); }
  .card--back { background: var(--card-light); }

  /* Firm name block */
  .firm {
    position: absolute; top: 58px; left: 0; right: 0;
    text-align: center; color: var(--brand-blue);
    font-family: "Cinzel", serif; font-weight: 700;
  }
  .firm__mark {
    display: block; width: 64px; height: 64px; margin: 0 auto 20px;
    background: var(--brand-blue);
  }
  .firm__name { font-size: 40px; line-height: 1; letter-spacing: 1px; }
  .firm__sub { font-size: 17px; line-height: 1.3; letter-spacing: 1px; margin-top: 4px; }
  .credentials {
    position: absolute; top: 236px; left: 0; right: 0; text-align: center;
    font-family: "Cinzel", serif; font-weight: 600;
    color: var(--muted-gray); font-size: 11.5px; letter-spacing: 1.2px; line-height: 1.35;
  }

  .person {
    position: absolute; top: 298px; left: 0; right: 0; text-align: center;
    font-family: "Cinzel", serif; font-weight: 700; color: var(--text-light);
  }
  .person__name { font-size: 28px; letter-spacing: 1px; }
  .person__title { font-size: 13px; letter-spacing: 1px; margin-top: 2px; }

  /* Contact list */
  .contacts {
    position: absolute; top: 405px; left: 52px; right: 40px;
    list-style: none; font-family: "Exo 2", sans-serif; color: var(--text-light);
  }
  .contacts__item {
    display: flex; align-items: center; gap: 18px;
    padding: 14px 0; border-bottom: 1px solid var(--rule-gray);
    font-size: 17px; letter-spacing: 1px;
  }
  .contacts__item:last-child { border-bottom: none; line-height: 1.25; }
  .contacts__icon { width: 22px; height: 22px; flex: none; fill: var(--text-light); }

  /* Bottom band with tab */
  .band { position: absolute; left: 0; bottom: 0; width: 434px; height: 100px; }
  .band__shape { fill: var(--band-gray); }
  .band__email {
    position: absolute; left: 0; right: 0; bottom: 28px; text-align: center;
    font-family: "Exo 2", sans-serif; font-size: 15px; letter-spacing: 0;
    color: var(--text-light); white-space: nowrap;
  }

  /* Back face */
  .back-firm {
    position: absolute; top: 270px; left: 0; right: 0; text-align: center;
    font-family: "Cinzel", serif; font-weight: 700; color: var(--brand-blue);
  }
  .back-firm__mark { display: block; width: 110px; height: 110px; margin: 0 auto 26px; background: var(--brand-blue); }
  .back-firm__name { font-size: 34px; letter-spacing: 1px; line-height: 1; }
  .back-firm__sub { font-size: 15px; letter-spacing: 1px; margin-top: 6px; }
</style>
</head>
<body>
<main class="sheet">

  <section class="card card--front" aria-label="Card front">
    <div class="firm">
      <span class="firm__mark" aria-hidden="true"></span>
      <div class="firm__name">PAVEL OSTROM</div>
      <div class="firm__sub">PROFESSIONAL CORPORATION</div>
    </div>
    <div class="credentials">
      CHARTERED PROFESSIONAL ACCOUNTANT<br>CERTIFIED GENERAL ACCOUNTANT
    </div>

    <div class="person">
      <div class="person__name">PAVEL OSTROM</div>
      <div class="person__title">CPA, CGA</div>
    </div>

    <ul class="contacts">
      <li class="contacts__item">
        <svg class="contacts__icon" viewBox="0 0 24 24" aria-hidden="true"><path d="M3 8c0-2 2-3 9-3s9 1 9 3v2h-4V8H7v2H3z"/><path d="M6 11h12l2 8H4z"/></svg>
        (416) 562-3907
      </li>
      <li class="contacts__item">
        <svg class="contacts__icon" viewBox="0 0 24 24" aria-hidden="true"><path d="M7 3h10v5H7z"/><path d="M3 9h18v8h-3v-3H6v3H3z"/><path d="M7 15h10v6H7z"/></svg>
        (416) 734-2165
      </li>
      <li class="contacts__item">
        <svg class="contacts__icon" viewBox="0 0 24 24" aria-hidden="true"><path d="M2 4h20v13H2zm2 2v9h16V6z"/><path d="M9 18h6v2H9z"/></svg>
        www.pavelostrom-example.ca
      </li>
      <li class="contacts__item">
        <svg class="contacts__icon" viewBox="0 0 24 24" aria-hidden="true"><path d="M12 3l10 9h-3v9h-5v-6h-4v6H5v-9H2z"/></svg>
        <span>47 Maple Crest Rd. Richmond Hill,<br>ON L7K 3B5</span>
      </li>
    </ul>

    <svg class="band" viewBox="0 0 434 100" aria-hidden="true">
      <path class="band__shape" d="M0 72H52Q62 72 66 62L72 46Q76 36 86 36H348Q358 36 362 46L368 62Q372 72 382 72H434V100H0Z"/>
    </svg>
    <div class="band__email">pavel@pavelostrom-example.ca</div>
  </section>

  <section class="card card--back" aria-label="Card back">
    <div class="back-firm">
      <span class="back-firm__mark" aria-hidden="true"></span>
      <div class="back-firm__name">PAVEL OSTROM</div>
      <div class="back-firm__sub">PROFESSIONAL CORPORATION</div>
    </div>
    <svg class="band" viewBox="0 0 434 100" aria-hidden="true">
      <path class="band__shape" d="M0 72H52Q62 72 66 62L72 46Q76 36 86 36H348Q358 36 362 46L368 62Q372 72 382 72H434V100H0Z"/>
    </svg>
    <div class="band__email">pavel@pavelostrom-example.ca</div>
  </section>

</main>
</body>
</html>
```